TalkHarbor - Language Coaching Services

Sleek, innovative, trendy design for Language Coaching business.

TalkHarbor is a new UK based company that provides Language Coaching services. We offer highly personalized on-line and face to face language courses. We also impart learning techniques workshops based on the latest neuroscience research for second-language acquisition.

Target Market(s)

See attached info

Industry/Entity Type

Consulting

Contact Information for Business Card

TalkHarbor
DaniaKV@talkharbor.co.uk
TalkHarbor.co.uk
London, UK

Font styles to use
Sans Serif

```html
<!DOCTYPE html>
<html lang="en">
<head>
<meta charset="utf-8">
<title>TalkHarbor – Business Card</title>
<link rel="stylesheet" href="https://fonts.googleapis.com/css2?family=Open+Sans:wght@400;600;700&display=swap">
<style>
  :root {
    --backdrop: #2a2c30;
    --card: #221f20;
    --brand-blue: #1a8fd0;
    --edge-blue: #1ea0e6;
    --text-light: #e8e8e8;
    --text-muted: #cfcfcf;
    --rule-white: #f2f2f2;
  }
  * { box-sizing: border-box; margin: 0; padding: 0; }
  html, body {
    width: 1200px; height: 900px; overflow: hidden;
    background: var(--backdrop);
    font-family: "Open Sans", Arial, sans-serif;
  }
  .stage {
    width: 1200px; height: 900px;
    display: flex; align-items: center; justify-content: center; gap: 60px;
  }
  .card {
    position: relative;
    width: 520px; height: 298px;
    background: var(--card);
    border-radius: 18px;
    overflow: hidden;
    box-shadow: 0 10px 30px rgba(0,0,0,.45);
  }
  .card--front { border-bottom: 8px solid var(--edge-blue); }

  /* wordmark */
  .wordmark { display: flex; align-items: center; gap: 12px; }
  .wordmark__circle {
    width: 58px; height: 58px; border-radius: 50%;
    border: 5px solid var(--brand-blue);
  }
  .wordmark__name {
    color: var(--brand-blue);
    font-weight: 600; font-size: 34px; letter-spacing: 1px;
  }
  .card--front .wordmark { position: absolute; left: 120px; top: 30px; }
  .card--back .wordmark {
    position: absolute; left: 50%; top: 96px; transform: translateX(-50%);
  }
  .card--back .wordmark__circle { width: 72px; height: 72px; border-width: 6px; }
  .card--back .wordmark__name { font-size: 40px; }

  .back-url {
    position: absolute; left: 0; right: 0; top: 196px;
    text-align: center; color: var(--text-light); font-size: 16px;
  }

  /* contact block */
  .contact { position: absolute; left: 30px; top: 118px; }
  .contact__company {
    color: var(--brand-blue); font-weight: 700; font-size: 16px; margin-bottom: 8px;
  }
  .contact__row {
    display: flex; align-items: center; gap: 10px;
    color: var(--text-light); font-size: 13px; line-height: 22px;
  }
  .icon { width: 13px; height: 13px; flex: none; fill: var(--brand-blue); }

  .divider {
    position: absolute; left: 150px; right: 0; top: 131px; height: 2px;
    background: linear-gradient(90deg, var(--brand-blue), var(--rule-white));
  }

  .address {
    position: absolute; right: 30px; bottom: 30px;
    display: flex; align-items: flex-end; gap: 10px;
    color: var(--text-light); font-size: 15px; line-height: 22px; text-align: right;
  }
  .address .icon { width: 14px; height: 18px; margin-bottom: 4px; }
</style>
</head>
<body>
<main class="stage">

  <section class="card card--front" aria-label="Business card front">
    <div class="wordmark">
      <span class="wordmark__circle"></span>
      <span class="wordmark__name">TALKHARBOR</span>
    </div>

    <div class="divider"></div>

    <div class="contact">
      <p class="contact__company">TalkHarbor</p>
      <p class="contact__row">
        <svg class="icon" viewBox="0 0 24 24"><path d="M6.6 10.8a15.1 15.1 0 0 0 6.6 6.6l2.2-2.2a1 1 0 0 1 1-.25 11.4 11.4 0 0 0 3.6.57 1 1 0 0 1 1 1V20a1 1 0 0 1-1 1A17 17 0 0 1 3 4a1 1 0 0 1 1-1h3.5a1 1 0 0 1 1 1c0 1.25.2 2.45.57 3.57a1 1 0 0 1-.25 1z"/></svg>
        +44 1632 960718
      </p>
      <p class="contact__row">
        <svg class="icon" viewBox="0 0 24 24"><path d="M2 5h20v14H2z M2 5l10 8 10-8" fill="none" stroke="#1a8fd0" stroke-width="2.4"/></svg>
        DaniaKV@talkharbor.co.uk
      </p>
      <p class="contact__row">
        <svg class="icon" viewBox="0 0 24 24"><circle cx="12" cy="12" r="10" fill="none" stroke="#1a8fd0" stroke-width="2.4"/><path d="M2 12h20M12 2c3 3 3 17 0 20M12 2c-3 3-3 17 0 20" fill="none" stroke="#1a8fd0" stroke-width="2"/></svg>
        www.talkharbor.co.uk
      </p>
    </div>

    <div class="address">
      <p>24 Harbour Lane,<br>TN33 4QX, London, UK</p>
      <svg class="icon" viewBox="0 0 24 30"><path d="M12 0a10 10 0 0 0-10 10c0 7.5 10 20 10 20s10-12.5 10-20A10 10 0 0 0 12 0zm0 14a4 4 0 1 1 0-8 4 4 0 0 1 0 8z"/></svg>
    </div>
  </section>

  <section class="card card--back" aria-label="Business card back">
    <div class="wordmark">
      <span class="wordmark__circle"></span>
      <span class="wordmark__name">TALKHARBOR</span>
    </div>
    <p class="back-url">www.talkharbor.co.uk</p>
  </section>

</main>
</body>
</html>
```